BOLD & MINIMALIST DESIGN NEEDED

We want a very bold but minimalistic business card design that is impactful and utilizes both sides of the business card. Our current logo is included for your use.

We want bold fonts and good use of negative space. We don't want the logo to overpower the design.

Target Market(s)

Professionals who are building new commercial buildings.

Industry/Entity Type

Construction

Contact Information for Business Card

Name, Title, email, office phone, cell phone, website

Font styles to use
Serif
Sans Serif

Requirements
Must have
• Bold design!

```html
<!DOCTYPE html>
<html lang="en">
<head>
<meta charset="utf-8">
<title>Summitcrest Design + Build — Business Card</title>
<link href="https://fonts.googleapis.com/css2?family=Roboto:wght@400;500;700&display=swap" rel="stylesheet">
<style>
  :root {
    --backdrop: #3b3b3b;
    --card-dark: #1a1a1a;
    --card-dark-mark: #2c2c2c;
    --card-light: #ffffff;
    --ink: #1b1b1b;
    --ink-soft: #333333;
    --accent: #8cc63f;
    --rule: #555555;
  }
  * { margin: 0; padding: 0; box-sizing: border-box; }
  html, body { width: 1200px; height: 694px; overflow: hidden; }
  body {
    background: var(--backdrop);
    font-family: "Roboto", Arial, sans-serif;
    display: flex;
    align-items: center;
    justify-content: center;
    gap: 60px;
  }
  .card {
    width: 500px;
    height: 286px;
    border-radius: 22px;
    position: relative;
    overflow: hidden;
  }
  .card--back {
    background: var(--card-dark);
    display: flex;
    align-items: center;
    justify-content: center;
  }
  .card--front {
    background: var(--card-light);
    display: flex;
    align-items: center;
  }
  .brand {
    display: flex;
    align-items: center;
    gap: 10px;
    font-weight: 700;
    text-transform: uppercase;
    letter-spacing: 0.5px;
  }
  .brand__square {
    width: 16px;
    height: 16px;
    background: currentColor;
    flex: none;
  }
  .card--back .brand { color: var(--card-dark-mark); font-size: 30px; }
  .card--front .brand { color: var(--ink); font-size: 22px; }
  .card--front .brand__square { background: var(--accent); }
  .brand-zone {
    width: 250px;
    display: flex;
    justify-content: center;
    padding-left: 14px;
  }
  .divider {
    width: 1px;
    height: 200px;
    background: linear-gradient(to bottom, var(--rule), rgba(85,85,85,0));
    flex: none;
  }
  .contact { padding-left: 22px; color: var(--ink-soft); }
  .contact__name { color: var(--accent); font-size: 22px; font-weight: 700; }
  .contact__title { font-size: 13px; margin: 2px 0 14px; }
  .contact__list { list-style: none; font-size: 12.5px; line-height: 1.65; }
  .contact__list li { display: flex; align-items: center; gap: 9px; }
  .contact__list svg { width: 13px; height: 13px; flex: none; fill: var(--ink); }
  .contact__address { font-size: 12.5px; line-height: 1.45; margin-top: 10px; }
</style>
</head>
<body>
  <section class="card card--back" aria-label="Card back">
    <div class="brand"><span class="brand__square"></span>Summitcrest Design + Build</div>
  </section>

  <section class="card card--front" aria-label="Card front">
    <div class="brand-zone">
      <div class="brand"><span class="brand__square"></span>Summitcrest</div>
    </div>
    <div class="divider"></div>
    <div class="contact">
      <p class="contact__name">Daniel Carver</p>
      <p class="contact__title">Owner</p>
      <ul class="contact__list">
        <li><svg viewBox="0 0 16 16" aria-hidden="true"><rect x="4" y="1" width="8" height="14" rx="1.5"/><rect x="5.5" y="3" width="5" height="8" fill="#fff"/></svg>044-987 654 321</li>
        <li><svg viewBox="0 0 16 16" aria-hidden="true"><path d="M3 2l3 0 1 3-2 1.5a9 9 0 0 0 4.5 4.5L11 9l3 1v3c0 1-1 2-2 2A12 12 0 0 1 1 4c0-1 1-2 2-2z"/></svg>044-987 654 321</li>
        <li><svg viewBox="0 0 16 16" aria-hidden="true"><path d="M1 3h14v10H1z"/><path d="M1.5 3.5L8 9l6.5-5.5" fill="none" stroke="#fff" stroke-width="1.3"/></svg>info@summitcrest.com</li>
        <li><svg viewBox="0 0 16 16" aria-hidden="true"><circle cx="8" cy="8" r="7"/><path d="M1 8h14M8 1c3 3 3 11 0 14M8 1c-3 3-3 11 0 14" fill="none" stroke="#fff" stroke-width="1"/></svg>www.summitcrest.com</li>
      </ul>
      <p class="contact__address">Address line goes here<br>45452, Country name</p>
    </div>
  </section>
</body>
</html>
```